Design wireframe of E-commerce website *

We are a European online shoe store located in Sweden. The project is to redesign the first page of our e-commerce website https://vantrel.se/skor
We want to receive creative ideas of what our website could look like while keeping all the functions and flows. The new design should be simple, lean and modern.
Specifications:
We have several guidelines for what we are expecting
- Redesign the frontend of our website first page https://vantrel.se/skor and the child page https://www.vantrel.se/skor/dam
- You need to provide a complete clickable wireframe of the target pages.
- All existing components should be in the new design.
- The pages should include all sections: header, footer, product lists and widgets. The page structure of the site should look as the example: https://www.pellimark.co.uk/shoes
- The design must be responsive and Mobile First which can be read from all browsers and different devices.
- You need to have in mind that we really want it to be mobile first, meaning
the mobile view is the most important one
- The new design should reflect our brands essence and come along with the new brandprofiles (fonts, icons...). For example http://brandprofile.pellimark.com/, but keep the logo and colour of the existing Vantrel theme.
- The design should be user friendly.
- The design should be simple enough that the pages can be downloaded fast.
- The new design should look fashionable and be able to generating attracting
traffic.
- The text on the child page https://www.vantrel.se/skor/dam should be handled in a better way and make it easier for users to know which page they are looking at. You can see the example at https://www.pellimark.co.uk/shoes/women but we are open to your good ideas as well.
- We do not want shelves in the design. Pellimark has it, but Vantrel
should not.
- We want to keep the existing responsive sizes for product list which means 2, 4 or 6 pairs of shoes per row.
Practical Information:
We are located in Sweden and have working hours between 9:00 -12:00 (CEST)
Monday - Friday. We have limited capacity to answer every question you have
but will try to get back to you in our working hours as much as we can then
hopefully this can help you get a better understanding of what we are
looking for.
Future Possibilities:We are going to redesign the whole site
of https://www.vantrel.se/skor so the winner
will have the chance to do all the pages in the near future. We are
actively seeking designers for future collaborations on a long-term basis
and it is possible to create a partnership if your work is impressive
enough. *

```html
<!DOCTYPE html>
<html lang="sv">
<head>
<meta charset="utf-8">
<title>Vantrel – Skor</title>
<link rel="stylesheet" href="https://fonts.googleapis.com/css2?family=Roboto:wght@300;400;500;700;900&display=swap">
<style>
:root{
  --page:#eceef1;
  --white:#ffffff;
  --ink:#1e1e22;
  --muted:#8a8a92;
  --line:#e3e3e8;
  --purple:#5a1d91;
  --purple-soft:#7a3fb5;
  --red:#d2232a;
  --hero-a:#3a2c22;
  --hero-b:#17120e;
  --footer:#0d0f16;
  --band:#f1f1f4;
}
*{box-sizing:border-box;margin:0;padding:0}
html,body{width:1200px;height:4455px;overflow:hidden}
body{background:var(--page);font-family:"Roboto",Arial,sans-serif;color:var(--ink);position:relative}
.abs{position:absolute}
.btn{display:inline-block;background:var(--purple);color:var(--white);font-weight:700;text-transform:uppercase;letter-spacing:.5px}
.photo{display:block}
.logo{font-weight:900;letter-spacing:1px;color:var(--white)}
.sec-title{position:absolute;left:0;right:0;text-align:center;text-transform:uppercase;color:#44444c;font-weight:400;letter-spacing:1px}

/* ---------- desktop ---------- */
.desktop{left:53px;top:42px;width:780px;height:2028px;background:var(--white);overflow:hidden;box-shadow:0 2px 14px rgba(0,0,0,.12)}
.d-hero{left:0;top:0;width:780px;height:308px;background:linear-gradient(110deg,var(--hero-a),#5a4333 45%,var(--hero-b))}
.d-shoe{right:150px;top:70px;width:200px;height:110px;border-radius:60px 90px 20px 20px;background:linear-gradient(160deg,#4a4d55,#23252b)}
.d-top{left:0;top:0;width:780px;height:60px;color:var(--white);font-size:9px}
.d-search{left:50px;top:16px;display:flex;align-items:center;gap:5px}
.d-logo{left:0;right:0;top:12px;text-align:center;font-size:20px}
.d-nav{right:40px;top:16px;display:flex;gap:14px}
.d-phone{right:40px;top:32px;font-weight:700}
.d-headline{left:60px;top:80px;color:var(--white)}
.d-headline .a{font-size:30px;font-weight:700}
.d-headline .b{font-size:58px;font-weight:500;line-height:1}
.d-buy{left:60px;top:228px;font-size:8px;padding:6px 14px}
.arrow{width:18px;height:18px;border-radius:50%;background:rgba(0,0,0,.55)}
.d-cats{left:107px;top:308px;width:567px;display:grid;grid-template-columns:repeat(4,1fr);background:var(--white);border:1px solid var(--line)}
.cat{height:112px;border:1px solid var(--line);display:flex;flex-direction:column;align-items:center;justify-content:center;gap:10px;font-size:8px;font-weight:700;text-transform:uppercase}
.cat .shoe{width:46px;height:34px;border-radius:6px}
.cat.is-active{background:#151515;color:var(--white)}
.cat small{color:var(--red);font-size:7px}
.d-sec{left:107px;width:567px}
.d-promo{top:730px;height:115px;display:flex}
.d-products{top:905px;display:grid;grid-template-columns:repeat(4,1fr);gap:4px 0}
.prod{position:relative;height:110px;padding:8px 10px}
.prod .corner{position:absolute;left:0;top:0}
.prod .shoe{width:60px;height:40px;margin:6px auto 10px;border-radius:6px}
.prod .row{display:flex;justify-content:space-between;font-size:8px}
.prod .name{font-weight:700}
.prod .sub{color:var(--muted);font-size:6px}
.prod .old{color:var(--red);font-size:7px}
.prod .now{color:var(--muted);font-size:7px}
.d-news{top:1195px;display:flex;gap:30px}
.news{flex:1;border-top:2px solid var(--purple);padding-top:6px;font-size:7px;color:#555;line-height:1.5}
.news b{color:var(--purple);display:block;font-size:8px}
.news .btn{margin-top:10px;font-size:6px;padding:4px 8px}
.d-fav{top:1362px;height:118px;display:flex}
.d-fav .photo{flex:1}
.tabs{display:flex;gap:10px;font-size:6px;color:var(--muted);text-transform:uppercase}
.tabs span{border-bottom:1px solid var(--line);padding-bottom:3px}
.tabs .on{color:var(--purple);border-bottom:2px solid var(--purple);font-weight:700}
.brands{display:flex;gap:4px}
.brand{flex:1;height:52px;background:var(--white);border:1px solid var(--line);display:flex;align-items:center;justify-content:center;font-weight:700;font-size:16px;color:var(--ink)}
.d-band{left:0;top:1620px;width:780px;height:150px;background:var(--band)}
.newsletter{display:flex;align-items:center;gap:8px;text-transform:uppercase;font-size:11px;color:#444}
.newsletter .input{background:var(--white);border:1px solid var(--line);font-size:7px;color:var(--muted);text-transform:none;padding:4px 8px}
.newsletter .btn{font-size:7px;padding:5px 14px}
.perks{display:flex;justify-content:space-between}
.perk{display:flex;flex-direction:column;align-items:center;gap:4px;font-size:6px;color:#444}
.d-footer{left:0;top:1790px;width:780px;height:238px;background:var(--footer);color:#c8c8d0;font-size:7px;line-height:1.7}
.foot-col b{color:var(--white);font-size:8px;display:block}
.badge{display:flex;align-items:center;gap:8px;color:var(--white);font-size:14px;font-weight:700}
.badge i{width:30px;height:30px;border-radius:50%;background:#e8b931;display:block}
.socials{display:flex;gap:6px;justify-content:center}
.socials i{width:12px;height:12px;border-radius:50%;border:1px solid #c8c8d0;display:block}

/* ---------- mobile ---------- */
.mobile{left:900px;top:134px;width:258px;height:4173px;background:var(--white);overflow:hidden;box-shadow:0 2px 14px rgba(0,0,0,.12)}
.m-head{left:0;top:0;width:258px;height:39px;background:var(--footer);text-align:center;padding-top:11px;font-size:15px}
.m-search{left:0;top:39px;width:258px;height:23px;border-bottom:1px solid var(--line);font-size:7px;display:flex;align-items:center;justify-content:center;gap:4px;color:#444}
.m-tools{left:0;top:62px;width:258px;height:36px;display:flex;justify-content:space-around;align-items:center;font-size:7px;color:#444}
.m-hero{left:0;top:98px;width:258px;height:170px;background:linear-gradient(110deg,var(--hero-a),#5a4333 50%,var(--hero-b))}
.m-headline{left:12px;top:20px;color:var(--white)}
.m-headline .a{font-size:17px;font-weight:700}
.m-headline .b{font-size:34px;font-weight:500;line-height:1}
.m-buy{left:12px;top:90px;font-size:6px;padding:4px 10px}
.m-cats{left:30px;top:228px;width:199px}
.m-cat{height:112px;border:1px solid var(--line);background:var(--white);display:flex;flex-direction:column;align-items:center;justify-content:center;gap:10px;font-size:7px;font-weight:700;text-transform:uppercase}
.m-cat .shoe{width:40px;height:30px;border-radius:6px}
.m-cat.is-active{background:#151515;color:var(--white)}
.m-cat small{color:var(--red);font-size:6px}
.m-sec{left:30px;width:199px}
.m-prod{position:relative;height:125px;border-bottom:1px solid var(--line);padding:8px 6px}
.m-prod .corner{position:absolute;left:0;top:0}
.m-prod .shoe{width:56px;height:38px;margin:8px auto 14px;border-radius:6px}
.m-prod .row{display:flex;justify-content:space-between;font-size:7px}
.m-prod .name{font-weight:700}
.m-prod .sub{color:var(--muted);font-size:5px}
.m-prod .old{color:var(--red);font-size:6px}
.m-prod .now{color:var(--muted);font-size:6px}
.m-news{font-size:6px;color:#555;line-height:1.5;border-top:2px solid var(--purple);padding-top:5px;margin-bottom:16px}
.m-news b{color:var(--purple);display:block;font-size:7px}
.m-news .btn{margin-top:6px;font-size:5px;padding:3px 7px}
.m-brand{height:56px;margin-bottom:6px;border:1px solid var(--line);display:flex;align-items:center;justify-content:center;font-weight:700;font-size:14px}
.m-band{left:0;top:3440px;width:258px;height:318px;background:var(--band)}
.m-footer{left:0;top:3758px;width:258px;height:415px;background:var(--footer);color:#c8c8d0;font-size:6px;line-height:1.7;padding:14px 12px}
.m-footer b{color:var(--white);font-size:7px;display:block}
</style>
</head>
<body>

<!-- ================= DESKTOP ================= -->
<main class="desktop abs">
  <section class="d-hero abs">
    <div class="photo abs" role="img" aria-label="Hero photo of leather shoes on a dark wooden floor with a grey running shoe" style="inset:0;background:linear-gradient(110deg,var(--hero-a),#5a4333 45%,var(--hero-b))"></div>
    <div class="d-shoe abs" role="img" aria-label="Grey running shoe"></div>
    <header class="d-top abs">
      <div class="d-search abs">
        <svg width="9" height="9" viewBox="0 0 10 10"><circle cx="4" cy="4" r="3" fill="none" stroke="#fff" stroke-width="1.2"/><line x1="6.3" y1="6.3" x2="9" y2="9" stroke="#fff" stroke-width="1.2"/></svg>
        Search here
      </div>
      <div class="d-logo logo abs">VANTREL</div>
      <nav class="d-nav abs"><span>Kart</span><span>Favoriter</span><span>Meny</span></nav>
      <div class="d-phone abs">+46 8 555 01 20</div>
    </header>
    <div class="d-headline abs"><div class="a">TUSENTALS SKOR</div><div class="b">50%- PA</div></div>
    <span class="d-buy btn abs">Buy now</span>
    <span class="arrow abs" style="left:14px;top:210px"></span>
    <span class="arrow abs" style="right:14px;top:210px"></span>
  </section>

  <section class="d-cats abs">
    <div class="cat is-active"><span class="shoe" role="img" aria-label="Ankle boot" style="background:#e9d9a8"></span>Stivaletter<small>från 499 kr</small></div>
    <div class="cat"><span class="shoe" role="img" aria-label="Sneaker" style="background:#2b2b2e"></span>Sneakers</div>
    <div class="cat"><span class="shoe" role="img" aria-label="Red pump" style="background:#c1243a"></span>Pingor</div>
    <div class="cat"><span class="shoe" role="img" aria-label="Brown boot" style="background:#5b3424"></span>Ekkor</div>
    <div class="cat"><span class="shoe" role="img" aria-label="Sports shoe" style="background:#d04672"></span>Sportskor</div>
    <div class="cat"><span class="shoe" role="img" aria-label="Black shoe" style="background:#1d1d20"></span>Blackskor</div>
    <div class="cat"><span class="shoe" role="img" aria-label="Purple heel" style="background:#7c2d6d"></span>Stovlar</div>
    <div class="cat"><span class="shoe" role="img" aria-label="Low shoe" style="background:#2a2a2d"></span>Lagskor</div>
    <div class="cat"><span class="shoe" role="img" aria-label="Sandal" style="background:#c9a27a"></span>Sandaler</div>
    <div class="cat"><span class="shoe" role="img" aria-label="Pink ballerina" style="background:#e0458c"></span>Ballerina</div>
    <div class="cat"><span class="shoe" role="img" aria-label="Red heel" style="background:#b51d2e"></span>Finskor</div>
    <div class="cat"><span class="shoe" role="img" aria-label="Red slipper" style="background:#c7313c"></span>Tofflor</div>
  </section>

  <h2 class="sec-title" style="top:690px;font-size:12px">Promotions</h2>
  <section class="d-sec d-promo abs">
    <div class="photo" role="img" aria-label="Colourful sandals and flats laid out on turquoise floor" style="flex:3;background:linear-gradient(120deg,#3ec0c9,#4fb3c2 50%,#e0a3a0);position:relative">
      <span class="abs" style="left:220px;top:30px;color:#fff;font-size:10px;line-height:1.4;letter-spacing:1px">SANDALER<br>FLIPFLOPS &amp; KILKLACK<br>SOMMARSKOR</span>
    </div>
    <div class="photo" role="img" aria-label="Woman in summer shoes on a dark background" style="flex:1;background:linear-gradient(160deg,#3a3a3a,#151515);position:relative">
      <span class="abs" style="left:12px;top:50px;color:#fff;font-size:8px">SOMMARSKOR</span>
    </div>
  </section>

  <h2 class="sec-title" style="top:872px;font-size:12px">Products</h2>
  <section class="d-sec d-products abs">
    <div class="prod"><svg class="corner" width="18" height="18"><polygon points="0,0 18,0 0,18" fill="var(--purple)"/></svg><div class="shoe" role="img" aria-label="Pink sports shoe" style="background:#d8457a"></div><div class="row"><span class="name">Sportskor</span><span class="old">129 kr</span></div><div class="row"><span class="sub">Damskor för fritid</span><span class="now">99 kr</span></div></div>
    <div class="prod"><svg class="corner" width="18" height="18"><polygon points="0,0 18,0 0,18" fill="var(--purple)"/></svg><div class="shoe" role="img" aria-label="Beige sandal" style="background:#d9c39a"></div><div class="row"><span class="name">Sandal</span><span class="old">129 kr</span></div><div class="row"><span class="sub">Damskor för fritid</span><span class="now">99 kr</span></div></div>
    <div class="prod"><svg class="corner" width="18" height="18"><polygon points="0,0 18,0 0,18" fill="var(--purple)"/></svg><div class="shoe" role="img" aria-label="Navy boot" style="background:#2d3b6a"></div><div class="row"><span class="name">Boots</span><span class="old">129 kr</span></div><div class="row"><span class="sub">Damskor för fritid</span><span class="now">99 kr</span></div></div>
    <div class="prod"><svg class="corner" width="18" height="18"><polygon points="0,0 18,0 0,18" fill="var(--purple)"/></svg><div class="shoe" role="img" aria-label="Red heel" style="background:#b51d2e"></div><div class="row"><span class="name">Lagskor</span><span class="old">129 kr</span></div><div class="row"><span class="sub">Damskor för fritid</span><span class="now">99 kr</span></div></div>
    <div class="prod"><svg class="corner" width="18" height="18"><polygon points="0,0 18,0 0,18" fill="var(--purple)"/></svg><div class="shoe" role="img" aria-label="Black sneaker" style="background:#2a2a2d"></div><div class="row"><span class="name">Sneakers</span><span class="old">129 kr</span></div><div class="row"><span class="sub">Damskor för fritid</span><span class="now">99 kr</span></div></div>
    <div class="prod"><svg class="corner" width="18" height="18"><polygon points="0,0 18,0 0,18" fill="var(--purple)"/></svg><div class="shoe" role="img" aria-label="Black low shoe" style="background:#1d1d20"></div><div class="row"><span class="name">Lagskor</span><span class="old">129 kr</span></div><div class="row"><span class="sub">Damskor för fritid</span><span class="now">99 kr</span></div></div>
    <div class="prod"><svg class="corner" width="18" height="18"><polygon points="0,0 18,0 0,18" fill="var(--purple)"/></svg><div class="shoe" role="img" aria-label="Dark brown boot" style="background:#3e2a22"></div><div class="row"><span class="name">Kängor</span><span class="old">129 kr</span></div><div class="row"><span class="sub">Damskor för fritid</span><span class="now">99 kr</span></div></div>
    <div class="prod"><svg class="corner" width="18" height="18"><polygon points="0,0 18,0 0,18" fill="var(--purple)"/></svg><div class="shoe" role="img" aria-label="Black heel" style="background:#141416"></div><div class="row"><span class="name">Finskor</span><span class="old">129 kr</span></div><div class="row"><span class="sub">Damskor för fritid</span><span class="now">99 kr</span></div></div>
  </section>

  <h2 class="sec-title" style="top:1160px;font-size:12px">News</h2>
  <section class="d-sec d-news abs">
    <article class="news"><b>Nya sommarskor har landat i butiken, se hela kollektionen nu.</b>Upptäck sandaler, espadriller och lätta sneakers för varma dagar. Fri frakt och fri retur på alla beställningar.<br><span class="btn">Läs mer</span></article>
    <article class="news"><b>Så väljer du rätt storlek när du handlar skor på nätet hos oss.</b>Vår storleksguide hjälper dig att hitta rätt passform för hela familjen. Byt enkelt om skon inte passar.<br><span class="btn">Läs mer</span></article>
  </section>

  <h2 class="sec-title" style="top:1335px;font-size:12px">Favorites</h2>
  <section class="d-sec d-fav abs">
    <div class="photo" role="img" aria-label="Feet in grey ankle boots" style="background:#8c8f86"></div>
    <div class="photo" role="img" aria-label="Feet in red shoes" style="background:#7a5a4c"></div>
    <div class="photo" role="img" aria-label="Green flats on pavement" style="background:#9a7f5c"></div>
    <div class="photo" role="img" aria-label="Feet in white sneakers on tiles" style="background:#3f8fb0"></div>
    <div class="photo" role="img" aria-label="Red sneakers on street" style="background:#6e6a66"></div>
    <div class="photo" role="img" aria-label="Heels on stone steps" style="background:#a49a8a"></div>
  </section>
  <nav class="d-sec tabs abs" style="top:1492px;justify-content:center"><span class="on">Stivaletter</span><span>Sneakers</span><span>Pingor</span><span>Ekkor</span><span>Sportskor</span><span>Stovlar</span><span>Lagskor</span><span>Finskor</span></nav>

  <section class="d-band abs"></section>
  <h2 class="sec-title" style="top:1560px;font-size:12px">Top brands</h2>
  <section class="d-sec brands abs" style="top:1592px">
    <div class="brand">Norrlid</div><div class="brand">Veltra</div><div class="brand">Kobbe</div><div class="brand">Stigra</div>
  </section>
  <section class="d-sec newsletter abs" style="top:1680px;justify-content:center">
    Subscribe newsletter <span class="input" style="width:180px">Enter your email</span><span class="btn">Subscribe</span>
  </section>
  <section class="d-sec perks abs" style="top:1715px;padding:0 40px">
    <div class="perk"><svg width="22" height="22" viewBox="0 0 22 22"><circle cx="11" cy="11" r="9" fill="none" stroke="var(--purple)" stroke-width="1.3"/><path d="M7 11l3 3 5-6" fill="none" stroke="var(--purple)" stroke-width="1.3"/></svg>Alltid 30 dagars öppet köp</div>
    <div class="perk"><svg width="22" height="22" viewBox="0 0 22 22"><rect x="2" y="7" width="11" height="8" fill="none" stroke="var(--purple)" stroke-width="1.3"/><path d="M13 10h4l3 3v2h-7z" fill="none" stroke="var(--purple)" stroke-width="1.3"/><circle cx="6" cy="17" r="1.6" fill="var(--purple)"/><circle cx="16" cy="17" r="1.6" fill="var(--purple)"/></svg>Alltid fri frakt och fri retur</div>
    <div class="perk"><svg width="22" height="22" viewBox="0 0 22 22"><path d="M11 2l7 3v6c0 5-3 8-7 9-4-1-7-4-7-9V5z" fill="none" stroke="var(--purple)" stroke-width="1.3"/></svg>Alltid prisgaranti</div>
  </section>

  <footer class="d-footer abs">
    <div class="foot-col abs" style="left:160px;top:22px"><b>Legal</b>Köpvillkor<br>Integritetspolicy<br>Cookies<br>Frakt<br>Returer</div>
    <div class="foot-col abs" style="left:250px;top:22px"><b>Contact Us</b>Storgatan 12, 111 22 Stockholm<br>Tel: +46 8 555 01 20<br>kund@vantrel.se</div>
    <div class="foot-col abs" style="left:380px;top:22px"><b>Vantrel.se</b>Om oss<br>Jobba hos oss<br>Presskontakt</div>
    <div class="badge abs" style="left:520px;top:40px"><i></i>Paylune</div>
    <div class="logo abs" style="left:0;right:0;top:150px;text-align:center;font-size:18px">VANTREL</div>
    <div class="socials abs" style="left:0;right:0;top:178px"><i></i><i></i><i></i></div>
    <div class="abs" style="left:0;right:0;top:198px;text-align:center;font-size:6px">© Vantrel AB, Storgatan 12, 111 22 Stockholm, org.nr 556000-0000, alla rättigheter förbehållna.</div>
  </footer>
</main>

<!-- ================= MOBILE ================= -->
<main class="mobile abs">
  <header class="m-head abs logo">VANTREL</header>
  <div class="m-search abs"><svg width="8" height="8" viewBox="0 0 10 10"><circle cx="4" cy="4" r="3" fill="none" stroke="#444" stroke-width="1.2"/><line x1="6.3" y1="6.3" x2="9" y2="9" stroke="#444" stroke-width="1.2"/></svg>Search here</div>
  <nav class="m-tools abs"><span>Kart</span><span>Favoriter</span><span>Meny</span></nav>
  <section class="m-hero abs" role="img" aria-label="Hero photo of leather shoes on a dark wooden floor">
    <div class="m-headline abs"><div class="a">TUSENTALS SKOR</div><div class="b">50%- PA</div></div>
    <span class="m-buy btn abs">Buy now</span>
  </section>

  <section class="m-cats abs">
    <div class="m-cat is-active"><span class="shoe" role="img" aria-label="Ankle boot" style="background:#e9d9a8"></span>Stivaletter<small>från 499 kr</small></div>
    <div class="m-cat"><span class="shoe" role="img" aria-label="Sneaker" style="background:#2b2b2e"></span>Sneakers</div>
    <div class="m-cat"><span class="shoe" role="img" aria-label="Red pump" style="background:#c1243a"></span>Pingor</div>
    <div class="m-cat"><span class="shoe" role="img" aria-label="Brown boot" style="background:#5b3424"></span>Ekkor</div>
    <div class="m-cat"><span class="shoe" role="img" aria-label="Sports shoe" style="background:#d04672"></span>Sportskor</div>
    <div class="m-cat"><span class="shoe" role="img" aria-label="Black shoe" style="background:#1d1d20"></span>Blackskor</div>
    <div class="m-cat"><span class="shoe" role="img" aria-label="Navy boot" style="background:#2d3b6a"></span>Stovlar</div>
    <div class="m-cat"><span class="shoe" role="img" aria-label="Low shoe" style="background:#2a2a2d"></span>Lagskor</div>
  </section>

  <h2 class="sec-title" style="top:1262px;font-size:9px">Promotions</h2>
  <div class="m-sec abs photo" role="img" aria-label="Colourful sandals and flats on turquoise floor" style="top:1292px;height:258px;background:linear-gradient(150deg,#3ec0c9,#49b6c4 55%,#e0a3a0)">
    <span class="abs" style="left:60px;top:150px;color:#fff;font-size:8px;line-height:1.4">SANDALER<br>FLIPFLOPS &amp; KILKLACK<br>SOMMARSKOR</span>
  </div>

  <h2 class="sec-title" style="top:1580px;font-size:9px">Products</h2>
  <section class="m-sec abs" style="top:1610px">
    <div class="m-prod"><svg class="corner" width="16" height="16"><polygon points="0,0 16,0 0,16" fill="var(--purple)"/></svg><div class="shoe" role="img" aria-label="Pink sports shoe" style="background:#d8457a"></div><div class="row"><span class="name">Sportskor</span><span class="old">129 kr</span></div><div class="row"><span class="sub">Damskor för fritid</span><span class="now">99 kr</span></div></div>
    <div class="m-prod"><svg class="corner" width="16" height="16"><polygon points="0,0 16,0 0,16" fill="var(--purple)"/></svg><div class="shoe" role="img" aria-label="Red heel" style="background:#b51d2e"></div><div class="row"><span class="name">Sportskor</span><span class="old">129 kr</span></div><div class="row"><span class="sub">Damskor för fritid</span><span class="now">99 kr</span></div></div>
    <div class="m-prod"><svg class="corner" width="16" height="16"><polygon points="0,0 16,0 0,16" fill="var(--purple)"/></svg><div class="shoe" role="img" aria-label="Navy boot" style="background:#2d3b6a"></div><div class="row"><span class="name">Sportskor</span><span class="old">129 kr</span></div><div class="row"><span class="sub">Damskor för fritid</span><span class="now">99 kr</span></div></div>
    <div class="m-prod"><svg class="corner" width="16" height="16"><polygon points="0,0 16,0 0,16" fill="var(--purple)"/></svg><div class="shoe" role="img" aria-label="Black low shoe" style="background:#1d1d20"></div><div class="row"><span class="name">Sportskor</span><span class="old">129 kr</span></div><div class="row"><span class="sub">Damskor för fritid</span><span class="now">99 kr</span></div></div>
    <div class="m-prod"><svg class="corner" width="16" height="16"><polygon points="0,0 16,0 0,16" fill="var(--purple)"/></svg><div class="shoe" role="img" aria-label="Black sneaker" style="background:#2a2a2d"></div><div class="row"><span class="name">Sportskor</span><span class="old">129 kr</span></div><div class="row"><span class="sub">Damskor för fritid</span><span class="now">99 kr</span></div></div>
  </section>

  <h2 class="sec-title" style="top:2268px;font-size:9px">News</h2>
  <section class="m-sec abs" style="top:2300px">
    <article class="m-news"><b>Nya sommarskor har landat i butiken, se hela kollektionen nu.</b>Upptäck sandaler och lätta sneakers för varma dagar.<br><span class="btn">Läs mer</span></article>
    <article class="m-news"><b>Så väljer du rätt storlek när du handlar skor på nätet.</b>Vår storleksguide hjälper dig att hitta rätt passform.<br><span class="btn">Läs mer</span></article>
  </section>

  <h2 class="sec-title" style="top:2580px;font-size:9px">Favorites</h2>
  <section class="m-sec abs" style="top:2610px">
    <div class="photo" role="img" aria-label="Feet in grey ankle boots" style="height:128px;background:#8c8f86;margin-bottom:6px"></div>
    <div class="photo" role="img" aria-label="Feet in red shoes" style="height:128px;background:#7a5a4c;margin-bottom:6px"></div>
    <div class="photo" role="img" aria-label="Green flats on pavement" style="height:128px;background:#9a7f5c"></div>
  </section>
  <nav class="m-sec tabs abs" style="top:3025px;gap:6px;font-size:5px"><span class="on">Stivaletter</span><span>Sneakers</span><span>Pingor</span><span>Ekkor</span></nav>

  <h2 class="sec-title" style="top:3122px;font-size:9px">Top brands</h2>
  <section class="m-sec abs" style="top:3152px;padding:0 25px">
    <div class="m-brand">Norrlid</div><div class="m-brand">Kobbe</div><div class="m-brand">Veltra</div><div class="m-brand">Stigra</div>
  </section>

  <section class="m-band abs">
    <div class="abs" style="left:12px;top:20px;font-size:9px;text-transform:uppercase;color:#444">Subscribe newsletter</div>
    <div class="newsletter abs" style="left:12px;top:42px;gap:0">
      <span class="input" style="width:160px;font-size:6px">Enter your email</span><span class="btn" style="font-size:6px;padding:4px 10px">Subscribe</span>
    </div>
    <div class="perk abs" style="left:0;right:0;top:85px"><svg width="30" height="30" viewBox="0 0 22 22"><circle cx="11" cy="11" r="9" fill="none" stroke="var(--purple)" stroke-width="1.2"/><path d="M7 11l3 3 5-6" fill="none" stroke="var(--purple)" stroke-width="1.2"/></svg>Alltid 30 dagars öppet köp</div>
    <div class="perk abs" style="left:0;right:0;top:160px"><svg width="30" height="30" viewBox="0 0 22 22"><rect x="2" y="7" width="11" height="8" fill="none" stroke="var(--purple)" stroke-width="1.2"/><path d="M13 10h4l3 3v2h-7z" fill="none" stroke="var(--purple)" stroke-width="1.2"/><circle cx="6" cy="17" r="1.6" fill="var(--purple)"/><circle cx="16" cy="17" r="1.6" fill="var(--purple)"/></svg>Alltid fri frakt och fri retur</div>
    <div class="perk abs" style="left:0;right:0;top:235px"><svg width="30" height="30" viewBox="0 0 22 22"><path d="M11 2l7 3v6c0 5-3 8-7 9-4-1-7-4-7-9V5z" fill="none" stroke="var(--purple)" stroke-width="1.2"/></svg>Alltid prisgaranti</div>
  </section>

  <footer class="m-footer abs">
    <b>Legal</b>Köpvillkor<br>Integritetspolicy<br>Cookies<br>Frakt<br>Returer<br><br>
    <b>Contact Us</b>Storgatan 12, 111 22 Stockholm<br>Tel: +46 8 555 01 20<br>kund@vantrel.se<br><br>
    <b>Vantrel.se</b>Om oss<br>Jobba hos oss<br>Presskontakt<br>Hjälp och support
    <div class="badge abs" style="right:14px;top:300px;font-size:11px"><i style="width:24px;height:24px"></i>Paylune</div>
    <div class="logo abs" style="left:0;right:0;top:345px;text-align:center;font-size:14px">VANTREL</div>
    <div class="socials abs" style="left:0;right:0;top:368px"><i></i><i></i><i></i></div>
    <div class="abs" style="left:12px;right:12px;top:385px;text-align:center;font-size:5px;line-height:1.5">© Vantrel AB, Storgatan 12, 111 22 Stockholm, alla rättigheter förbehållna.</div>
  </footer>
</main>

</body>
</html>
```